NZ First of it's kind solutions directory and marketplace for busy Mums needs a business card design

We need a business card design for our new nationwide business in NZ (long term plans to go global). We provide solutions to the everyday challenges that busy Mums face by connecting them with quality communities and suppliers of carefully selected, relevant products and services. We sell direct via our online marketplace. The final design should communicate our values of inclusivity, quality and smart solutions. Colours should incorporate our logo colour palette of #477077 and #6ba8b2. Our website is at https://www.brightnestmums.example

Target Market(s)

busy Mums, Age 28 – 50, female, income over $100K, location main centres NZ primarily but NZ wide. Is likely juggling work or career with a young family. Probably had hobbies which have fallen by the wayside.
-Wants to succeed in her chosen career without compromising on family life
-to successfully juggle her career without feeling like she is compromising her children
- Is time poor, something always has to give and it’s generally her health (she’ll stay up late, get stressed)
- probably ex corporate or professional career. Has discretional income

Industry/Entity Type

Business

Contact Information for Business Card

Lena Forbisher, Founder, BrightNestMums.example (Strapline Tap; Gather; Sorted), 47 Kowhai Terrace, Ellerslie, Auckland 1051, New Zealand. Mob: 021 483 517 Ph: +64 (0)9 571 4860

Font styles to use
Other font styles liked:
• Raleway, and/or Architects Daughter

Colors
00a990
33b8a4
86cfc6
cfeae6

Requirements
Must have
• the above details, streamline. the logo and colours associated with those logos
Should not have
• foil or metallic colours

```html
<!DOCTYPE html>
<html lang="en">
<head>
<meta charset="utf-8">
<title>BrightNestMums — Business Card</title>
<link rel="stylesheet" href="https://fonts.googleapis.com/css2?family=Arimo:wght@400;700&display=swap">
<style>
  :root {
    --stage: #1e1e1e;
    --card: #ffffff;
    --teal-deep: #477077;
    --teal-light: #6ba8b2;
    --ink: #222222;
    --ink-soft: #444444;
    --rule: #8fc0c8;
  }
  * { margin: 0; padding: 0; box-sizing: border-box; }
  html, body {
    width: 1200px; height: 900px; overflow: hidden;
    background: var(--stage);
    font-family: "Arimo", Arial, sans-serif;
  }
  .canvas { position: relative; width: 1200px; height: 900px; }
  .card {
    position: absolute; top: 170px; width: 347px; height: 561px;
    box-shadow: 3px 4px 8px rgba(0,0,0,0.6);
    overflow: hidden;
  }
  .card--front { left: 259px; background: var(--card); }
  .card--back { left: 631px; }

  .brand {
    position: absolute; top: 174px; left: 0; width: 100%; height: 36px;
    display: flex; align-items: center; justify-content: center; gap: 12px;
  }
  .brand__dot { width: 30px; height: 30px; border-radius: 50%; background: var(--teal-deep); flex: none; }
  .brand__name { font-size: 28px; line-height: 36px; font-weight: 700; color: var(--teal-deep); letter-spacing: -0.3px; }

  .contact {
    position: absolute; top: 343px; left: 0; width: 100%;
    text-align: center; color: var(--ink);
  }
  .contact__name { font-size: 20px; font-weight: 700; color: var(--ink-soft); line-height: 24px; }
  .contact__name .first { color: var(--teal-deep); }
  .contact__role { font-size: 15px; line-height: 18px; color: var(--ink-soft); }
  .contact__rule { width: 141px; height: 1px; background: var(--rule); margin: 7px auto 6px; }
  .contact__rule--lower { margin: 11px auto 14px; }
  .contact__line { font-size: 16px; line-height: 20px; }
  .contact__line b { color: var(--teal-deep); }
  .contact__address { font-size: 16px; line-height: 20px; }

  .back__art {
    position: absolute; inset: 0;
    background: linear-gradient(180deg, var(--teal-deep) 0%, var(--teal-deep) 52%, var(--teal-light) 58%, var(--teal-light) 100%);
  }
  .back__url {
    position: absolute; top: 315px; left: 0; width: 100%;
    text-align: center; font-size: 20px; line-height: 24px; font-weight: 700; color: #ffffff;
  }
</style>
</head>
<body>
<main class="canvas">
  <section class="card card--front">
    <div class="brand">
      <span class="brand__dot"></span>
      <span class="brand__name">BrightNestMums</span>
    </div>
    <div class="contact">
      <p class="contact__name"><span class="first">LENA</span> FORBISHER</p>
      <p class="contact__role">Founder</p>
      <div class="contact__rule"></div>
      <p class="contact__line"><b>P:</b> 021 483 517</p>
      <p class="contact__line"><b>M:</b> +64 (0)9 571 4860</p>
      <p class="contact__line"><b>W:</b> www.BrightNestMums.example</p>
      <div class="contact__rule contact__rule--lower"></div>
      <p class="contact__address">47 Kowhai Terrace, Ellerslie<br>Auckland 1051, New Zealand</p>
    </div>
  </section>

  <section class="card card--back">
    <div class="back__art" role="img" aria-label="Brand colour field in deep and light teal"></div>
    <p class="back__url">www.BrightNestMums.example</p>
  </section>
</main>
</body>
</html>
```